Design a modern, classy & professional business card for an online real estate agency, specializing in medium-luxury properties in Thailand and later in Singapore and UK.

Possible design ideas so far: (not essential)

- curved corner(s) to the card, white on front & turquoise on back or visa versa.

- front of card - clear and simple, company name in metallic grey/monochrome, logo graphic & company name on front in spot UV or embossed/debossed effect.

- back of card - large, close-cropped, 'ghost' patterns of the C-shaped curves of logo, or company name repeated on back of card in spot UV.

Target Market(s)

- young to middle-aged professionals mainly (but ideally should design should suit all)

- UK, US,EU,AUS & ASIAN mainly (but ideally should design should suit all countries)

Industry/Entity Type

Real Estate

Requirements
Must have
• THEME:
- Luxurious & Modern
- Clean & striking
- Unique & creative

INFO:
- Logo & company name on front
- Contact details on back:

Tobias Hennlund
Managing Director

www.velmontestates.asia
www.velmontestates.co.uk

Tel: 083-274-6159
email: tobias@velmontestates.asia

(contact details can be displayed in any order as suites design.)

Nice to have
• - curved corner(s) to the card, white on front & turquoise on back or visa versa.

Should not have
• - No generic images of properties, palm trees/coconut trees etc.

- No other other bold colors, except for main turquoise, grey, metallic white & black theme.

- No obvious business card templates

```html
<!DOCTYPE html>
<html lang="en">
<head>
<meta charset="utf-8">
<title>Velmont Estates – Business Card</title>
<link rel="stylesheet" href="https://fonts.googleapis.com/css2?family=Tinos&family=Arimo&display=swap">
<style>
  :root {
    --stage-light: #8e8e8e;
    --stage-dark: #262626;
    --turquoise: #1fc4bd;
    --turquoise-soft: #9be5e0;
    --turquoise-ghost: #d2f3f1;
    --card-white: #ffffff;
    --metal-grey: #6f6f6f;
    --rule-grey: #a9a9a9;
    --ink: #1a1111;
  }
  * { box-sizing: border-box; margin: 0; padding: 0; }
  html, body { width: 1200px; height: 889px; overflow: hidden; }
  body {
    background: radial-gradient(ellipse 60% 70% at 42% 55%, var(--stage-light), var(--stage-dark));
    font-family: "Tinos", "Times New Roman", serif;
    position: relative;
  }
  .card {
    position: absolute;
    width: 712px;
    height: 406px;
    border-radius: 62px;
    overflow: hidden;
  }
  .card--back {
    left: 85px; top: 62px;
    background: var(--turquoise-soft);
  }
  .card--front {
    left: 425px; top: 407px;
    background: var(--card-white);
  }
  .ghost-field {
    position: absolute; inset: 0;
  }
  .card--back .ghost-field {
    background: radial-gradient(ellipse 70% 80% at 70% 30%, #b4ece8, var(--turquoise-soft) 70%);
  }
  .card--front .ghost-field {
    background: radial-gradient(ellipse 60% 90% at 85% 60%, var(--turquoise-ghost), rgba(255,255,255,0) 75%);
  }
  .brand {
    position: absolute;
    display: flex;
    align-items: center;
    color: var(--metal-grey);
  }
  .brand__square {
    background: var(--turquoise);
    flex: none;
  }
  .brand__name { line-height: 1; font-weight: 400; }
  .brand__name span { display: block; }
  .card--back .brand { left: 144px; top: 144px; gap: 16px; }
  .card--back .brand__square { width: 117px; height: 118px; }
  .card--back .brand__word { font-size: 80px; }
  .card--back .brand__sub { font-size: 30px; letter-spacing: 5px; margin-top: 4px; padding-left: 8px; }
  .card--front .brand { left: 355px; top: 25px; gap: 14px; }
  .card--front .brand__square { width: 88px; height: 88px; }
  .card--front .brand__word { font-size: 60px; }
  .card--front .brand__sub { font-size: 22px; letter-spacing: 3.5px; margin-top: 2px; padding-left: 4px; }
  .accent-line {
    position: absolute; left: 0; top: 72px;
    width: 340px; height: 3px;
    background: var(--rule-grey);
  }
  .person {
    position: absolute; left: 0; right: 0; top: 186px;
    text-align: center; color: var(--ink);
    padding-right: 8px;
  }
  .person__name { font-size: 40px; line-height: 1; font-weight: 400; }
  .person__title { font-size: 25px; line-height: 1; margin-top: 10px; }
  .contact {
    position: absolute; left: 40px; top: 311px; width: 630px; height: 66px;
    border-top: 1px solid var(--ink);
    border-bottom: 1px solid var(--ink);
    font-family: "Arimo", Arial, sans-serif;
    font-size: 18px; line-height: 24px; color: #000;
    display: flex; justify-content: space-between;
    padding: 8px 0 0 3px;
  }
  .contact__label { display: inline-block; width: 56px; }
</style>
</head>
<body>
  <section class="card card--back">
    <div class="ghost-field" role="img" aria-label="Faint large curved pattern in pale turquoise"></div>
    <div class="brand">
      <div class="brand__square"></div>
      <h1 class="brand__name"><span class="brand__word">Velmont</span><span class="brand__sub">ESTATES</span></h1>
    </div>
  </section>

  <section class="card card--front">
    <div class="ghost-field" role="img" aria-label="Faint large curved pattern in pale turquoise"></div>
    <div class="accent-line"></div>
    <div class="brand">
      <div class="brand__square"></div>
      <p class="brand__name"><span class="brand__word">Velmont</span><span class="brand__sub">ESTATES</span></p>
    </div>
    <div class="person">
      <h2 class="person__name">Tobias Hennlund</h2>
      <p class="person__title">Managing Director</p>
    </div>
    <div class="contact">
      <div class="contact__direct">
        <p><span class="contact__label">Tel</span>: 083-274-6159</p>
        <p>email : tobias@velmontestates.asia</p>
      </div>
      <div class="contact__web">
        <p>www.velmontestates.asia</p>
        <p>www.velmontestates.co.uk</p>
      </div>
    </div>
  </section>
</body>
</html>
```